Business card for a Exhibition booth fabrication company

Hi. My company would like to change our corporate name card. We are an events and Exhibition stand builder company. We would like our corporate name card to resonate what we do. I need someone to create something unique that relates to the industry that I am in. The graphic designer should be creative to incorporate the elements of my industry and try to blend in well in the design of the card. Our aim is to ensure that we are unique and our card can look different from our competitors.
Updates

Target Market(s)

Marketing and events manager from all companies

Contact Information for Business Card

The business card should have the following details:
Name
Job Title
Email
Website

Colors

Designer to choose colors to be used in the design.

Requirements
Must have
• The card must be look something that is relevant to the service that I am providing. My website is: www.velmora-buildworks.com
• You can see my website to get more information on what service that I am doing
Nice to have
• On the back of my card, I would like to have a globe image with the incorporation of my company logo. This is to indicate that my services can be done in any part of the world.

```html
<!DOCTYPE html>
<html lang="en">
<head>
<meta charset="UTF-8">
<title>Velmora Buildworks – Business Card</title>
<link rel="stylesheet" href="https://fonts.googleapis.com/css2?family=Montserrat:wght@500;600&family=Open+Sans:wght@400;600&display=swap">
<style>
  :root {
    --stage: #2b2b2c;
    --card-grey: #5f6062;
    --card-white: #ffffff;
    --brand-red: #e31b23;
    --text-light: #f2f2f2;
    --text-dark: #5a5a5c;
  }
  * { box-sizing: border-box; margin: 0; padding: 0; }
  html, body {
    width: 1200px; height: 900px; overflow: hidden;
    background: var(--stage);
  }
  .canvas {
    position: relative; width: 1200px; height: 900px;
    display: flex; flex-direction: column; align-items: center; justify-content: center; gap: 60px;
  }
  .card {
    position: relative; width: 560px; height: 320px;
    border-radius: 18px; overflow: hidden;
    background: var(--card-grey);
    box-shadow: 0 10px 24px rgba(0,0,0,.45);
  }
  .card-front__curve {
    position: absolute; inset: 0; width: 100%; height: 100%;
  }
  .contact {
    position: absolute; left: 30px; top: 46px; width: 222px;
    color: var(--text-light);
    font-family: "Open Sans", Arial, sans-serif;
  }
  .contact__name {
    font-family: "Montserrat", Arial, sans-serif;
    font-weight: 600; font-size: 20px; letter-spacing: 1.5px; text-transform: uppercase;
    white-space: nowrap;
  }
  .contact__title { font-size: 13px; margin-top: 2px; }
  .contact__address { font-size: 12px; line-height: 17px; margin-top: 14px; }
  .contact__list { list-style: none; margin-top: 8px; font-size: 12px; line-height: 20px; }
  .contact__list li { display: flex; align-items: center; gap: 7px; white-space: nowrap; }
  .contact__list svg { width: 10px; height: 10px; flex: none; }
  .brand {
    position: absolute; display: flex; align-items: center;
    font-family: "Montserrat", Arial, sans-serif;
    font-weight: 500; text-transform: uppercase; white-space: nowrap;
  }
  .brand__dot { border-radius: 50%; background: var(--brand-red); flex: none; }
  .brand--front {
    left: 300px; right: 18px; top: 92px;
    flex-direction: column; gap: 10px;
    font-size: 14px; letter-spacing: 2px; color: var(--text-dark);
  }
  .brand--front .brand__dot { width: 32px; height: 32px; }
  .brand--back {
    left: 50%; top: 50%; transform: translate(-50%, -50%);
    flex-direction: column; gap: 16px;
    font-size: 24px; letter-spacing: 3px; color: var(--text-light);
  }
  .brand--back .brand__dot { width: 60px; height: 60px; }
</style>
</head>
<body>
<main class="canvas">
  <section class="card card-front" aria-label="Business card front">
    <svg class="card-front__curve" viewBox="0 0 560 320" preserveAspectRatio="none" aria-hidden="true">
      <path d="M330 0 C255 70 250 230 350 320 L560 320 L560 0 Z" fill="var(--card-white)"/>
      <path d="M318 0 C243 70 238 235 338 320" fill="none" stroke="var(--brand-red)" stroke-width="5"/>
    </svg>
    <div class="contact">
      <h1 class="contact__name">Daniel Reyes</h1>
      <p class="contact__title">Director</p>
      <p class="contact__address">P.O. Box 2184 Marina Road<br>Doha - Qatar</p>
      <ul class="contact__list">
        <li><svg viewBox="0 0 12 12"><path d="M3 1 L5 3.5 L4 5 Q5.5 7.5 7 8 L8.5 7 L11 9 L9.5 11 Q3 10 1 2.5 Z" fill="currentColor"/></svg>+65 91874402</li>
        <li><svg viewBox="0 0 12 12"><rect x="3" y="0.5" width="6" height="11" rx="1.2" fill="none" stroke="currentColor" stroke-width="1.2"/><circle cx="6" cy="9.5" r=".7" fill="currentColor"/></svg>+974 55302218</li>
        <li><svg viewBox="0 0 12 12"><rect x="0.6" y="2.2" width="10.8" height="7.6" fill="none" stroke="currentColor" stroke-width="1.2"/><path d="M0.6 2.2 L6 6.5 L11.4 2.2" fill="none" stroke="currentColor" stroke-width="1.2"/></svg>info@velmora-buildworks.com</li>
        <li><svg viewBox="0 0 12 12"><circle cx="6" cy="6" r="5.2" fill="none" stroke="currentColor" stroke-width="1.2"/><ellipse cx="6" cy="6" rx="2.2" ry="5.2" fill="none" stroke="currentColor" stroke-width="1"/><path d="M1 6 H11" stroke="currentColor" stroke-width="1"/></svg>www.velmora-buildworks.com</li>
      </ul>
    </div>
    <div class="brand brand--front"><span class="brand__dot"></span><span>Velmora Buildworks</span></div>
  </section>

  <section class="card card-back" aria-label="Business card back">
    <div class="brand brand--back"><span class="brand__dot"></span><span>Velmora Buildworks</span></div>
  </section>
</main>
</body>
</html>
```